Website design for an Italian restaurant in Amsterdam

I need a design for a client of mine. It is for Teatro Lucerna, an Italian restaurant in Amsterdam.
We are going for a clean, modern look but we also need to realise an authentic feel.
The restaurant is located in an old movie theatre, that is where the name Teatro Lucerna comes from.
Industry/Entity Type
Italian Restaurant
Number of Pages Required
1 page
Font styles to use
Sans Serif
Colors
Designer to choose colors to be used in the design.

```html
<!DOCTYPE html>
<html lang="en">
<head>
<meta charset="utf-8">
<title>Teatro Lucerna – Italian Restaurant</title>
<link rel="stylesheet" href="https://fonts.googleapis.com/css2?family=Montserrat:wght@400;500;600;700;800&family=Open+Sans:wght@400;600;700&display=swap">
<style>
:root{
  --black:#000;
  --footer:#1d1d1d;
  --blue:#1ba3df;
  --yellow:#eef40b;
  --white:#fff;
  --muted:#cfcfcf;
  --dark-text:#222;
  --dish-bg:#2c2c2c;
}
*{margin:0;padding:0;box-sizing:border-box}
html,body{width:1200px;height:3005px;overflow:hidden}
body{position:relative;background:var(--black);color:var(--white);font-family:"Open Sans",Arial,sans-serif}
.abs{position:absolute}
.pill{position:absolute;background:var(--yellow);color:#333;border-radius:22px;display:flex;align-items:center;justify-content:center;font-size:13px;font-family:"Open Sans",Arial,sans-serif}
.center{left:0;width:1200px;text-align:center}

/* header */
.site-header{position:absolute;left:0;top:0;width:1200px;height:110px;background:var(--black)}
.search{left:186px;top:28px;display:flex;align-items:center;gap:10px;font-size:12px;letter-spacing:.5px}
.logo{top:22px;font-family:"Montserrat",Arial,sans-serif;font-weight:600;font-size:27px;letter-spacing:.5px}
.socials{left:910px;top:32px;display:flex;gap:12px}
.socials span{width:14px;height:14px;background:var(--white);border-radius:2px;display:block}
.nav{top:86px;display:flex;justify-content:center;font-size:13px}
.nav a{color:var(--white);text-decoration:none;padding:0 10px 8px;position:relative}
.nav a.active{color:var(--yellow);border-bottom:2px solid var(--yellow)}
.nav .caret{font-size:8px;vertical-align:middle}

/* hero */
.hero{position:absolute;left:0;top:110px;width:1200px;height:592px;background:radial-gradient(ellipse at 50% 35%,#5a3f2b 0%,#35261b 45%,#170f0a 100%)}
.hero-welcome{top:284px;font-family:"Montserrat",Arial,sans-serif;font-weight:700;font-size:17px}
.hero-title{top:314px;font-family:"Montserrat",Arial,sans-serif;font-weight:700;font-size:38px}
.hero-sub{top:358px;font-family:"Montserrat",Arial,sans-serif;font-weight:700;font-size:26px}
.hero-text{top:396px;font-size:13px;font-weight:700}

/* sections */
.band-blue{position:absolute;left:0;width:1200px;background:var(--blue)}
.section-title{font-family:"Montserrat",Arial,sans-serif;font-weight:500;font-size:27px;letter-spacing:4px}
.about-text{left:246px;width:708px;top:818px;font-size:10.5px;line-height:20px;text-align:center}

/* reservation */
.res-title{left:190px;top:1128px;font-family:"Montserrat",Arial,sans-serif;font-weight:500;font-size:26px;letter-spacing:2px}
.field{position:absolute;left:190px;width:372px;border-bottom:2px solid var(--muted);font-size:11px;padding-bottom:6px}
.res-photo{left:600px;top:1124px;width:408px;height:408px;background:radial-gradient(ellipse at 50% 40%,#6b4a2c 0%,#3a2718 50%,#140c07 100%)}

/* menu */
.dish{position:absolute;top:1736px;width:200px}
.dish .photo{width:200px;height:200px;background:linear-gradient(160deg,#3a3a3a 0%,var(--dish-bg) 100%)}
.dish .name{margin-top:12px;font-size:10px;font-weight:700}
.dish .desc{margin-top:2px;font-size:10px;white-space:nowrap}
.arrow{position:absolute;font-size:34px;line-height:1}

/* blogs */
.blog{position:absolute;top:2246px;width:262px;height:328px;background:var(--white);border-radius:8px;overflow:hidden;color:var(--dark-text)}
.blog .photo{height:168px;border:2px solid var(--white);border-radius:8px 8px 0 0}
.blog h3{margin:22px 0 0 22px;font-family:"Montserrat",Arial,sans-serif;font-size:17px;font-weight:600}
.blog .meta{margin:10px 22px 0;display:flex;justify-content:space-between;font-size:10px}
.blog p{margin:8px 22px 0;font-size:10px;line-height:15px}
.blog .more{margin:8px 22px 0;font-size:10px;font-weight:700}

/* footer */
.site-footer{position:absolute;left:0;top:2732px;width:1200px;height:273px;background:var(--footer)}
.foot-logo{left:190px;top:2774px;font-family:"Montserrat",Arial,sans-serif;font-weight:700;font-size:26px;color:var(--yellow)}
.foot-text{font-size:10.5px;line-height:15px}
.foot-head{font-family:"Montserrat",Arial,sans-serif;font-weight:700;font-size:12px;color:var(--yellow);letter-spacing:.5px}
.foot-links{left:476px;top:2818px;font-size:10.5px;line-height:20px}
.contact-row{position:absolute;left:600px;display:flex;gap:12px;font-size:10.5px;line-height:15px;align-items:flex-start}
.circle{width:20px;height:20px;border-radius:50%;background:var(--yellow)}
</style>
</head>
<body>

<header class="site-header">
  <div class="abs search">
    <svg width="18" height="18" viewBox="0 0 18 18"><circle cx="7" cy="7" r="5.5" fill="none" stroke="#fff" stroke-width="2"/><line x1="11" y1="11" x2="16.5" y2="16.5" stroke="#fff" stroke-width="2"/></svg>
    <span>SEARCH</span>
  </div>
  <div class="abs center logo">YOUR LOGO</div>
  <div class="abs socials"><span></span><span></span><span></span><span></span></div>
  <nav class="abs center nav">
    <a class="active">Home</a><a>Menu <span class="caret">▼</span></a><a>Reservation</a><a>Pages <span class="caret">▼</span></a><a>About</a><a>Contact</a>
  </nav>
</header>

<section class="hero" role="img" aria-label="Dimly lit restaurant dining room inside an old movie theatre with a projection screen and string lights"></section>
<div class="abs center hero-welcome">WELCOME TO</div>
<h1 class="abs center hero-title">ITALIAN RESTAURANT</h1>
<h2 class="abs center hero-sub">TEATRO LUCERNA</h2>
<p class="abs center hero-text">Lorem Ipsum is simply dummy text of the printing and typesetting industry.</p>
<div class="pill" style="left:510px;top:434px;width:178px;height:42px">Reservation</div>
<svg class="abs" style="left:590px;top:610px" width="20" height="40" viewBox="0 0 20 40"><rect x="2" y="2" width="16" height="36" rx="8" fill="none" stroke="#eef40b" stroke-width="3"/><line x1="10" y1="10" x2="10" y2="20" stroke="#eef40b" stroke-width="3"/></svg>

<section class="band-blue" style="top:702px;height:352px"></section>
<h2 class="abs center section-title" style="top:760px">About</h2>
<p class="abs about-text">Lorem Ipsum is simply dummy text of the printing and typesetting industry. Lorem Ipsum has been the industry's standard dummy text ever since the 1500s, when an unknown printer took a galley of type and scrambled it to make a type specimen book. It has survived not only five centuries, but also the leap into electronic typesetting, remaining essentially unchanged. It was popularised in the 1960s with the release of Letraset sheets containing Lorem Ipsum passages, and more recently with desktop publishing software like Aldus PageMaker including versions of Lorem Ipsum.</p>
<div class="pill" style="left:512px;top:952px;width:178px;height:42px">Read More</div>

<h2 class="abs res-title">Make Online Reservation</h2>
<div class="field" style="top:1180px">Full Name</div>
<div class="field" style="top:1228px">E-Mail</div>
<div class="field" style="top:1278px">Phone Number</div>
<div class="field" style="top:1326px">Number Of People</div>
<div class="field" style="top:1382px">Date Book</div>
<div class="field" style="top:1430px">Time</div>
<div class="pill" style="left:190px;top:1492px;width:178px;height:40px">Reservation</div>
<div class="abs res-photo" role="img" aria-label="Warmly lit restaurant interior with set tables and folded napkins"></div>

<section class="band-blue" style="top:1628px;height:490px"></section>
<h2 class="abs center section-title" style="top:1670px">MENU</h2>
<div class="arrow" style="left:82px;top:1846px">←</div>
<div class="arrow" style="left:1084px;top:1846px;color:var(--yellow)">→</div>
<div class="dish" style="left:194px"><div class="photo" role="img" aria-label="Plate of spaghetti with tomatoes and basil on a dark table"></div><div class="name">SPEGHITY</div><div class="desc">Lorem Ipsum is simply dummy text .</div></div>
<div class="dish" style="left:400px"><div class="photo" role="img" aria-label="Plate of lasagna with tomato sauce on a dark table"></div><div class="name">LASAGNA</div><div class="desc">Lorem Ipsum is simply dummy text .</div></div>
<div class="dish" style="left:606px"><div class="photo" role="img" aria-label="Pizza with tomato and basil on a wooden board"></div><div class="name">PIZZA</div><div class="desc">Lorem Ipsum is simply dummy text .</div></div>
<div class="dish" style="left:812px"><div class="photo" role="img" aria-label="Plate of penne pasta with vegetables on a dark table"></div><div class="name">PASTA</div><div class="desc">Lorem Ipsum is simply dummy text .</div></div>
<div class="pill" style="left:512px;top:2034px;width:178px;height:40px">View All Menu</div>

<h2 class="abs center section-title" style="top:2172px">Latest Blogs</h2>
<div class="arrow" style="left:82px;top:2418px">←</div>
<div class="arrow" style="left:1084px;top:2418px;color:var(--yellow)">→</div>
<article class="blog" style="left:190px">
  <div class="photo" role="img" aria-label="Salad bowl with vegetables on a wooden table" style="background:linear-gradient(135deg,#7a4a2a,#c98a4a 50%,#5f7f3a)"></div>
  <h3>BLOG 1</h3>
  <div class="meta"><span>▦ 19.6.2018</span><span>◯ 12 Comments</span></div>
  <p>Lorem Ipsum is simply dummy text of the printing and typesetting industry.</p>
  <div class="more" style="color:var(--yellow)">READ MORE...</div>
</article>
<article class="blog" style="left:466px">
  <div class="photo" role="img" aria-label="Spaghetti with meatballs in tomato sauce" style="background:linear-gradient(135deg,#3a3a3a,#c9843e 50%,#8a2a1e)"></div>
  <h3>BLOG 2</h3>
  <div class="meta"><span>▦ 19.6.2018</span><span>◯ 12 Comments</span></div>
  <p>Lorem Ipsum is simply dummy text of the printing and typesetting industry.</p>
  <div class="more">READ MORE...</div>
</article>
<article class="blog" style="left:744px">
  <div class="photo" role="img" aria-label="Table set with shared Italian dishes" style="background:linear-gradient(135deg,#d8cbb8,#b07850 50%,#e9e1d4)"></div>
  <h3>BLOG 3</h3>
  <div class="meta"><span>▦ 19.6.2018</span><span>◯ 12 Comments</span></div>
  <p>Lorem Ipsum is simply dummy text of the printing and typesetting industry.</p>
  <div class="more">READ MORE...</div>
</article>
<div class="pill" style="left:512px;top:2630px;width:178px;height:42px">View More</div>

<footer class="site-footer"></footer>
<div class="abs foot-logo">YOUR LOGO</div>
<p class="abs foot-text" style="left:190px;top:2818px;width:230px">Lorem Ipsum is simply dummy text of the printing and typesetting industry.</p>
<div class="abs foot-text" style="left:190px;top:2862px;font-weight:700">READ MORE...</div>
<div class="abs" style="left:190px;top:2888px;display:flex;gap:8px"><span class="circle"></span><span class="circle"></span><span class="circle"></span><span class="circle"></span></div>

<div class="abs foot-head" style="left:476px;top:2786px">QUICK LINK</div>
<div class="abs foot-links">Home<br>Menu<br>Resrevation<br>Blogs<br>Contact</div>

<div class="abs foot-head" style="left:602px;top:2786px">QUICK LINK</div>
<div class="contact-row" style="top:2822px"><svg width="12" height="16" viewBox="0 0 12 16"><path d="M6 0a6 6 0 0 0-6 6c0 4.5 6 10 6 10s6-5.5 6-10a6 6 0 0 0-6-6z" fill="#eef40b"/><circle cx="6" cy="6" r="2.2" fill="#1d1d1d"/></svg><span>42 Lantern Lane Harbor,<br>NL 1015</span></div>
<div class="contact-row" style="top:2862px"><svg width="14" height="14" viewBox="0 0 14 14"><path d="M3 0l3 3-2 2c1 2 3 4 5 5l2-2 3 3-2 3C6 14 0 8 0 3z" fill="#eef40b"/></svg><span>+012-555-0142</span></div>
<div class="contact-row" style="top:2892px"><svg width="14" height="10" viewBox="0 0 14 10"><rect width="14" height="10" fill="#eef40b"/><path d="M0 0l7 6 7-6" fill="none" stroke="#1d1d1d" stroke-width="1.4"/></svg><span>info@teatrolucerna.com</span></div>

<div class="abs foot-head" style="left:800px;top:2786px">SUBSCRIBE</div>
<p class="abs foot-text" style="left:800px;top:2818px;width:215px">Lorem Ipsum is simply dummy text of the printing and typesetting industry.</p>
<div class="abs" style="left:798px;top:2876px;width:212px;height:28px;background:var(--white);display:flex;align-items:center;justify-content:space-between">
  <span style="font-size:10px;color:#aaa;padding-left:12px">Email Address</span>
  <span style="width:46px;height:28px;background:var(--yellow);display:flex;align-items:center;justify-content:center"><svg width="16" height="14" viewBox="0 0 16 14"><path d="M0 6L16 0 12 14 8 9 14 2 6 8z" fill="#222"/></svg></span>
</div>
<div class="abs" style="left:190px;top:2934px;width:820px;height:2px;background:var(--white)"></div>
<div class="abs foot-text" style="left:190px;top:2948px">© Copyright 2018 Italian Resrurent - All Right Reserved</div>
<div class="abs foot-text" style="left:820px;top:2948px;width:190px;text-align:right">Privacy Policy - Terms &amp; conditions</div>

</body>
</html>
```